Stationery Design Project for Strelvo, Chicago

Strelvo, a street parking application which helps car drivers find a street parking spot by offering an ideal path along which to look for parking. This path is calculated by our algorithm based on data (e.g. historical data, baseball games schedule, etc.). Along this path the driver will find a spot and will also save 70% of the search time. Customer we target is reg. between 21 and 45 yo.

We envision something young, fresh, bright and original. Slightly abstract maybe. It should represent the idea and elements of finding street parking in the city, e.g. car(s), parking spot, people, city, etc. (just ideas!).

Logo is attached.

Requirement:
- Business Cards (2 Sided Full Color CMYK)
- Letterhead (1 Sided Full Color CMYK)
- Envelope (1 Sided Full Color CMYK)
- Sticker (1 Sided Full Color CMYK), round with a 2inch diameter.

Reason: We're starting to get more and more designs and need more time to look into all of them. Very exciting!! Thanks to everybody!

Hi all, we're in the process of selecting our favs. Though choices!!! Really good submissions. Will keep you posted and sorry for the delay.

Target Market(s)

Car drivers and owners between 21 and 45

Industry/Entity Type

Parking

Requirements
Must have
• Sticker should be round and include company URL strelvo.com and the new logo which we will attach soon.
Should not have
• Should not be too serious or boring.

```html
<!DOCTYPE html>
<html lang="en">
<head>
<meta charset="utf-8">
<title>Strelvo – Business Card</title>
<link href="https://fonts.googleapis.com/css2?family=Source+Sans+3:wght@400;600;700&display=swap" rel="stylesheet">
<style>
  :root{
    --backdrop:#b08323;
    --card:#ffffff;
    --brand-blue:#1b4fa6;
    --brand-cyan:#0aaeea;
    --accent:#1a9ad9;
    --ink:#2b2b2b;
    --ink-dark:#3a2a10;
  }
  *{margin:0;padding:0;box-sizing:border-box}
  html,body{width:1200px;height:686px;overflow:hidden;background:var(--backdrop)}
  .stage{position:relative;width:1200px;height:686px;background:var(--backdrop);font-family:"Source Sans 3",sans-serif;color:var(--ink)}
  .card{position:absolute;width:462px;height:264px;border-radius:19px;background:var(--card);overflow:hidden;box-shadow:2px 3px 4px rgba(0,0,0,.45)}
  .card-front{left:123px;top:102px}
  .card-back{left:605px;top:371px;width:461px;height:263px;background:radial-gradient(ellipse at 50% 40%,#ffffff 30%,#ececec 75%)}
  .card-shade{position:absolute;left:0;top:0;width:100%;height:100%}
  .edge-band{position:absolute;right:0;top:0;width:22px;height:100%;background:linear-gradient(180deg,var(--brand-blue) 0%,var(--brand-cyan) 55%,var(--brand-blue) 100%)}
  .brand{position:absolute;display:flex;align-items:center;gap:16px}
  .brand-front{left:86px;top:40px}
  .brand-mark{width:80px;height:80px;border-radius:50%;background:var(--brand-blue);flex:none}
  .brand-name{font-size:50px;font-weight:600;color:var(--ink);letter-spacing:-0.5px;line-height:1}
  .contact{position:absolute;left:0;width:440px;top:172px;text-align:center}
  .contact-name{font-size:16px;font-weight:700;color:var(--accent);line-height:1.2}
  .contact-name span{font-size:12px;color:var(--ink-dark)}
  .contact-line{font-size:12.5px;line-height:1.2;margin-top:6px;display:flex;justify-content:center;gap:14px;align-items:center}
  .contact-line .item{display:inline-flex;align-items:center;gap:3px}
  .contact-line svg{width:11px;height:11px;fill:var(--accent)}
  .brand-back{position:absolute;left:0;width:100%;top:24px;display:flex;flex-direction:column;align-items:center;gap:10px}
  .brand-back .brand-mark{width:112px;height:112px;box-shadow:0 0 0 5px #f4f4f4,0 0 0 6px #dcdcdc}
  .brand-back .brand-name{font-size:28px}
</style>
</head>
<body>
<main class="stage">
  <section class="card card-front">
    <svg class="card-shade" viewBox="0 0 462 264" preserveAspectRatio="none">
      <defs>
        <linearGradient id="frontShade" x1="0" y1="0" x2="0" y2="1">
          <stop offset="0" stop-color="#e8e8e8"/>
          <stop offset="0.75" stop-color="#efefef"/>
          <stop offset="1" stop-color="#ffffff"/>
        </linearGradient>
      </defs>
      <path d="M0 195 Q231 100 462 195 L462 264 L0 264Z" fill="url(#frontShade)"/>
    </svg>
    <div class="brand brand-front">
      <div class="brand-mark"></div>
      <div class="brand-name">strelvo</div>
    </div>
    <div class="contact">
      <div class="contact-name">Your Name<span>, Title</span></div>
      <div class="contact-line">Street name City, State, zip code</div>
      <div class="contact-line">
        <span class="item"><svg viewBox="0 0 24 24"><path d="M6.6 10.8a15 15 0 0 0 6.6 6.6l2.2-2.2c.3-.3.7-.4 1-.2 1.1.4 2.3.6 3.6.6.6 0 1 .4 1 1V20c0 .6-.4 1-1 1A17 17 0 0 1 3 4c0-.6.4-1 1-1h3.5c.6 0 1 .4 1 1 0 1.3.2 2.5.6 3.6.1.3 0 .7-.2 1z"/></svg>123-456-7890</span>
        <span class="item"><svg viewBox="0 0 24 24"><path d="M6 2h10v6H6zM3 9h18v9h-3v4H6v-4H3zM8 15v5h8v-5z"/></svg>123-456-7890</span>
      </div>
      <div class="contact-line">
        <span class="item"><svg viewBox="0 0 24 24"><path d="M2 5h20v14H2zM3 6l9 7 9-7"/></svg>name@website.com</span>
        <span class="item"><svg viewBox="0 0 24 24"><path d="M12 2a10 10 0 1 0 0 20 10 10 0 0 0 0-20zm6.9 9h-3a15 15 0 0 0-1.3-6 8 8 0 0 1 4.3 6zM12 4c.9 1.2 1.7 3.8 1.9 7h-3.8c.2-3.2 1-5.8 1.9-7zM9.4 5a15 15 0 0 0-1.3 6h-3a8 8 0 0 1 4.3-6zM5.1 13h3a15 15 0 0 0 1.3 6 8 8 0 0 1-4.3-6zm5 0h3.8c-.2 3.2-1 5.8-1.9 7-.9-1.2-1.7-3.8-1.9-7zm4.5 6a15 15 0 0 0 1.3-6h3a8 8 0 0 1-4.3 6z"/></svg>www.website.com</span>
      </div>
    </div>
    <div class="edge-band"></div>
  </section>

  <section class="card card-back">
    <svg class="card-shade" viewBox="0 0 461 263" preserveAspectRatio="none">
      <defs>
        <linearGradient id="backShade" x1="0" y1="0" x2="0" y2="1">
          <stop offset="0" stop-color="#dadada"/>
          <stop offset="1" stop-color="#f2f2f2"/>
        </linearGradient>
      </defs>
      <path d="M0 225 Q230 140 461 225 L461 263 L0 263Z" fill="url(#backShade)"/>
    </svg>
    <div class="brand-back">
      <div class="brand-mark"></div>
      <div class="brand-name">strelvo</div>
    </div>
  </section>
</main>
</body>
</html>
```